Supplement Company needs final product mockups and label design

We're a Supplement company launching 4 Hydration Supplement flavours. We need someone to re create the EXACT design with what ChatGPT has already generated and tweak the design slightly so that spelling is correct and callout icons are designed. We then also need someone to do the back of label design that includes space for the barcode, nutrition table, blurb etc. Bonus if you have experience with PLDMQ compliance regulations and designing supplement labels.

We want the other 3 flavours (Lime, Mango & Watermelon) to match the design of the strawberry flavour including details like all the callout icons on the left side of the front, the word "electrolytes" in the dark coloured box, the words "hydration powder" just above the callout icons. Please re - design the callout icons to better suit the callout.

I've also attached an image of what the nutrition label should look like.

Please include the Following on the back of the label:
"Directions: Mix 1 Scoop with 400-500ml of water & Mix well before drinking. Do not exceed 2 servings per day.

Why rest when you can KORVA?
Your body wasn’t made to run on sugar, chemicals, and artificial junk — and your hydration shouldn’t either. At KORVA Nutrition, we’ve created a clean, mineral-rich formula with Brindlemoor Flakes and essential electrolytes to fuel you the right way. No toxins, no fillers — just real ingredients that work with your body, not against it.
Drink the way earth designed. Stay pure. KORVA.

AUSTRALIAN OWNED AND MADE

Store in a cool, dry place below 30°C. Reseal after use"

Product Formula & Ingredients:

* Sodium (Sea Salt, Brindlemoor Flakes®, Himalayan Pink Salt): 1000 mg
* Potassium (from Potassium Chloride): 200 mg
* Magnesium (from Magnesium Glycinate): 60 mg
* Total Carbohydrates: 0 g
* Sugars: 0 g
* Calories: 1 kcal

Ingredients:
Sea Salt, Citric Acid, Brindlemoor Flakes®, Himalayan Pink Salt, Potassium Chloride, Magnesium Glycinate, Natural Flavour (e.g. Mango), Stevia Leaf Extract.
Updates

I would like to give designers more time to closely replicate what I have included in the brief and make sure they can create something very beautifully

Industry/Entity Type

Supplements

Font styles to use
Other font styles liked:
• Montserrat

Requirements
Must have
• Back of label design aswell and Australian Nutrition table
Nice to have
• Design as close to the Provided images as possible
Should not have
• Should not be too different to the attached images

```html
<!DOCTYPE html>
<html lang="en">
<head>
<meta charset="utf-8">
<title>KORVA Nutrition – Electrolytes Hydration Powder Labels</title>
<link rel="stylesheet" href="https://fonts.googleapis.com/css2?family=Montserrat:wght@500;600;700;800&family=Oswald:wght@500;600;700&display=swap">
<style>
:root{
  --ink-dark:#111111;
  --ink-mid:#262626;
  --white:#ffffff;
  --table-ink:#1a1a1a;
  --badge-green:#1f7a3a;
  --badge-gold:#f2c230;
}
.flavour--strawberry{--label-a:#e0262c;--label-b:#9c0f14;--box:#5c0a0d;--fruit-a:#ff4b4b;--fruit-b:#b30d16;--stage-a:#c4141b;--stage-b:#5e0508;--row-bg:#c8142a;}
.flavour--lime{--label-a:#a9d13a;--label-b:#5f9416;--box:#3a5a0e;--fruit-a:#c6ef6a;--fruit-b:#4e8a12;--stage-a:#6aa61e;--stage-b:#2f5c0a;--row-bg:#a7cd33;}
.flavour--mango{--label-a:#f7a21f;--label-b:#d9600c;--box:#7a3606;--fruit-a:#ffd23a;--fruit-b:#f0741a;--stage-a:#e8900f;--stage-b:#a2500a;--row-bg:#f4a11c;}
.flavour--watermelon{--label-a:#ee4a7d;--label-b:#b81848;--box:#6a0f2e;--fruit-a:#ff5a5a;--fruit-b:#2f8a2f;--stage-a:#e8457c;--stage-b:#b01448;--row-bg:#e5407a;}

*{box-sizing:border-box;margin:0;padding:0}
html,body{width:1200px;height:4286px;overflow:hidden}
body{font-family:"Montserrat",sans-serif;color:var(--white);background:var(--ink-dark);position:relative}

/* ---------- Hero ---------- */
.hero{position:absolute;left:0;top:0;width:1200px;height:1165px;background:linear-gradient(180deg,#2e2e2e 0%,#161616 60%,#0b0b0b 100%)}
.hero-brand{position:absolute;top:58px;left:0;width:100%;text-align:center;font-weight:800}
.hero-brand__name{font-size:112px;line-height:1;letter-spacing:.02em}
.hero-brand__sub{font-size:36px;letter-spacing:.14em;margin-top:6px}
.hero-shelf{position:absolute;left:0;top:955px;width:100%;height:2px;background:#3a3a3a}
.hero-lineup{position:absolute;left:0;top:440px;width:100%;display:flex;justify-content:center;gap:36px;font-size:15.5px}
.hero-title{position:absolute;left:0;top:1058px;width:100%;text-align:center;font-size:58px;font-weight:700;letter-spacing:.03em}

/* ---------- Flavour stages ---------- */
.stage-grid{position:absolute;left:0;top:1165px;width:1200px;height:1203px;display:grid;grid-template-columns:600px 600px;grid-template-rows:601px 602px}
.stage{display:flex;align-items:center;justify-content:center;font-size:16px;background:radial-gradient(circle at 50% 45%,var(--stage-a) 0%,var(--stage-b) 100%)}

/* ---------- Label rows ---------- */
.label-row{position:absolute;left:0;width:1200px;height:479px;background:var(--row-bg)}
.label-row--1{top:2368px}.label-row--2{top:2847px}.label-row--3{top:3326px}.label-row--4{top:3805px;height:481px}
.label-row .back-label{position:absolute;left:87px;top:90px}
.label-row .front-label{position:absolute;left:846px;top:88px;font-size:16px}

/* ---------- Front label ---------- */
.front-label{width:16em;height:19em;border-radius:.35em;background:linear-gradient(135deg,var(--label-a),var(--label-b));color:var(--white);display:flex;flex-direction:column;align-items:center;padding:1.1em .9em .8em;overflow:hidden;box-shadow:0 .3em .9em rgba(0,0,0,.25)}
.front-label--inset{background:none;box-shadow:none}
.brand{font-size:2.2em;font-weight:800;line-height:1;letter-spacing:.04em}
.brand-sub{font-size:.62em;font-weight:600;letter-spacing:.22em;margin-top:.15em}
.flavour-name{font-family:"Oswald",sans-serif;font-weight:700;font-size:2.35em;line-height:1.05;letter-spacing:.01em;margin-top:.08em}
.electrolytes-box{font-size:.95em;font-weight:700;letter-spacing:.08em;background:var(--box);padding:.12em .55em;border-radius:.2em;margin-top:.15em}
.format{font-size:.62em;font-weight:600;letter-spacing:.06em;margin-top:.55em}
.label-body{flex:1;width:100%;display:flex;align-items:center;justify-content:space-between;padding:0 .2em}
.callouts{list-style:none;display:flex;flex-direction:column;gap:.35em}
.callouts li{display:flex;align-items:center;gap:.35em;font-size:.45em;font-weight:600;line-height:1.15}
.callout-icon{width:2.4em;height:2.4em;flex:none}
.fruit-art{width:6.6em;height:6.6em;border-radius:50%;background:radial-gradient(circle at 40% 35%,var(--fruit-a) 0%,var(--fruit-b) 85%)}
.net-weight{font-family:"Oswald",sans-serif;font-weight:600;font-size:.9em;letter-spacing:.04em}

/* ---------- Back label ---------- */
.back-label{width:753px;height:300px;background:linear-gradient(135deg,var(--label-a),var(--label-b));display:grid;grid-template-columns:250px 250px 253px;overflow:hidden;box-shadow:0 6px 18px rgba(0,0,0,.2)}
.back-copy{padding:16px 10px 12px 14px;font-size:7.2px;line-height:1.38;font-weight:500}
.back-copy p{margin-bottom:4px}
.back-copy strong{font-weight:800}
.back-copy .store{text-align:center;margin-top:4px}
.back-front{display:flex;justify-content:center;align-items:flex-start;padding-top:10px;font-size:14.5px}
.back-panel{padding:20px 12px 10px 6px;display:flex;flex-direction:column;gap:6px}
.back-panel__top{display:flex;gap:6px;align-items:flex-start}
.nutrition{background:var(--white);color:var(--table-ink);width:176px;padding:5px 6px;font-size:5.6px;line-height:1.3}
.nutrition__title{font-size:7.4px;font-weight:800;border-bottom:1px solid var(--table-ink);padding-bottom:2px;margin-bottom:2px}
.nutrition table{width:100%;border-collapse:collapse}
.nutrition th{font-weight:700;text-align:right;border-bottom:.8px solid var(--table-ink);padding:1px 0}
.nutrition th:first-child{text-align:left}
.nutrition td{padding:1px 0;border-bottom:.5px solid #bbb;text-align:right}
.nutrition td:first-child{text-align:left}
.nutrition .sub td:first-child{padding-left:6px}
.made-badge{width:26px;height:34px;background:var(--badge-green);border:2px solid var(--badge-gold);border-radius:3px;flex:none}
.ingredients{font-size:7.2px;line-height:1.4;font-weight:500}
.ingredients strong{font-weight:800}

/* ---------- Icon palette ---------- */
.icon-bg{fill:var(--white)}
.icon-mark{fill:none;stroke:var(--ink-mid);stroke-width:1.8;stroke-linecap:round;stroke-linejoin:round}
</style>
</head>
<body>

<svg width="0" height="0" style="position:absolute" aria-hidden="true">
  <defs>
    <symbol id="icon-keto" viewBox="0 0 24 24">
      <circle class="icon-bg" cx="12" cy="12" r="11"/>
      <path class="icon-mark" d="M12 5.5c2.8 3.5 4.5 6 4.5 8.3a4.5 4.5 0 0 1-9 0c0-2.3 1.7-4.8 4.5-8.3z"/>
    </symbol>
    <symbol id="icon-sugar" viewBox="0 0 24 24">
      <circle class="icon-bg" cx="12" cy="12" r="11"/>
      <rect class="icon-mark" x="7.5" y="7.5" width="9" height="9" rx="1"/>
      <path class="icon-mark" d="M5.5 18.5l13-13"/>
    </symbol>
    <symbol id="icon-paleo" viewBox="0 0 24 24">
      <circle class="icon-bg" cx="12" cy="12" r="11"/>
      <path class="icon-mark" d="M7 17c0-6 4-10 10-10 0 6-4 10-10 10z"/>
      <path class="icon-mark" d="M7 17l6-6"/>
    </symbol>
    <symbol id="icon-gluten" viewBox="0 0 24 24">
      <circle class="icon-bg" cx="12" cy="12" r="11"/>
      <circle class="icon-mark" cx="12" cy="12" r="6.5"/>
      <path class="icon-mark" d="M7.4 16.6l9.2-9.2"/>
    </symbol>
  </defs>
</svg>

<!-- Hero -->
<section class="hero">
  <div class="hero-brand">
    <div class="hero-brand__name">KORVA</div>
    <div class="hero-brand__sub">NUTRITION</div>
  </div>

  <div class="hero-lineup">
    <div class="front-label flavour--strawberry">
      <div class="brand">KORVA</div><div class="brand-sub">NUTRITION</div>
      <div class="flavour-name">STRAWBERRY</div>
      <div class="electrolytes-box">ELECTROLYTES</div>
      <div class="format">HYDRATION POWDER</div>
      <div class="label-body">
        <ul class="callouts">
          <li><svg class="callout-icon"><use href="#icon-keto"/></svg><span>KETO<br>FRIENDLY</span></li>
          <li><svg class="callout-icon"><use href="#icon-sugar"/></svg><span>SUGAR<br>FREE</span></li>
          <li><svg class="callout-icon"><use href="#icon-paleo"/></svg><span>PALEO<br>FRIENDLY</span></li>
          <li><svg class="callout-icon"><use href="#icon-gluten"/></svg><span>GLUTEN<br>FREE</span></li>
        </ul>
        <div class="fruit-art" role="img" aria-label="Illustration of a ripe strawberry"></div>
      </div>
      <div class="net-weight">NET WT. 180g</div>
    </div>
    <div class="front-label flavour--mango">
      <div class="brand">KORVA</div><div class="brand-sub">NUTRITION</div>
      <div class="flavour-name">MANGO</div>
      <div class="electrolytes-box">ELECTROLYTES</div>
      <div class="format">HYDRATION POWDER</div>
      <div class="label-body">
        <ul class="callouts">
          <li><svg class="callout-icon"><use href="#icon-keto"/></svg><span>KETO<br>FRIENDLY</span></li>
          <li><svg class="callout-icon"><use href="#icon-sugar"/></svg><span>SUGAR<br>FREE</span></li>
          <li><svg class="callout-icon"><use href="#icon-paleo"/></svg><span>PALEO<br>FRIENDLY</span></li>
          <li><svg class="callout-icon"><use href="#icon-gluten"/></svg><span>GLUTEN<br>FREE</span></li>
        </ul>
        <div class="fruit-art" role="img" aria-label="Illustration of a ripe mango"></div>
      </div>
      <div class="net-weight">NET WT. 180g</div>
    </div>
    <div class="front-label flavour--lime">
      <div class="brand">KORVA</div><div class="brand-sub">NUTRITION</div>
      <div class="flavour-name">LIME</div>
      <div class="electrolytes-box">ELECTROLYTES</div>
      <div class="format">HYDRATION POWDER</div>
      <div class="label-body">
        <ul class="callouts">
          <li><svg class="callout-icon"><use href="#icon-keto"/></svg><span>KETO<br>FRIENDLY</span></li>
          <li><svg class="callout-icon"><use href="#icon-sugar"/></svg><span>SUGAR<br>FREE</span></li>
          <li><svg class="callout-icon"><use href="#icon-paleo"/></svg><span>PALEO<br>FRIENDLY</span></li>
          <li><svg class="callout-icon"><use href="#icon-gluten"/></svg><span>GLUTEN<br>FREE</span></li>
        </ul>
        <div class="fruit-art" role="img" aria-label="Illustration of a halved lime"></div>
      </div>
      <div class="net-weight">NET WT. 180g</div>
    </div>
    <div class="front-label flavour--watermelon">
      <div class="brand">KORVA</div><div class="brand-sub">NUTRITION</div>
      <div class="flavour-name">WATERMELON</div>
      <div class="electrolytes-box">ELECTROLYTES</div>
      <div class="format">HYDRATION POWDER</div>
      <div class="label-body">
        <ul class="callouts">
          <li><svg class="callout-icon"><use href="#icon-keto"/></svg><span>KETO<br>FRIENDLY</span></li>
          <li><svg class="callout-icon"><use href="#icon-sugar"/></svg><span>SUGAR<br>FREE</span></li>
          <li><svg class="callout-icon"><use href="#icon-paleo"/></svg><span>PALEO<br>FRIENDLY</span></li>
          <li><svg class="callout-icon"><use href="#icon-gluten"/></svg><span>GLUTEN<br>FREE</span></li>
        </ul>
        <div class="fruit-art" role="img" aria-label="Illustration of a watermelon slice"></div>
      </div>
      <div class="net-weight">NET WT. 180g</div>
    </div>
  </div>

  <div class="hero-shelf"></div>
  <h1 class="hero-title">HYDRATION POWDER</h1>
</section>

<!-- Flavour stages -->
<section class="stage-grid">
  <div class="stage flavour--strawberry" role="img" aria-label="Strawberry label with splashing red juice and fresh strawberries">
    <div class="front-label">
      <div class="brand">KORVA</div><div class="brand-sub">NUTRITION</div>
      <div class="flavour-name">STRAWBERRY</div>
      <div class="electrolytes-box">ELECTROLYTES</div>
      <div class="format">HYDRATION POWDER</div>
      <div class="label-body">
        <ul class="callouts">
          <li><svg class="callout-icon"><use href="#icon-keto"/></svg><span>KETO<br>FRIENDLY</span></li>
          <li><svg class="callout-icon"><use href="#icon-sugar"/></svg><span>SUGAR<br>FREE</span></li>
          <li><svg class="callout-icon"><use href="#icon-paleo"/></svg><span>PALEO<br>FRIENDLY</span></li>
          <li><svg class="callout-icon"><use href="#icon-gluten"/></svg><span>GLUTEN<br>FREE</span></li>
        </ul>
        <div class="fruit-art" role="img" aria-label="Illustration of a ripe strawberry"></div>
      </div>
      <div class="net-weight">NET WT. 180g</div>
    </div>
  </div>
  <div class="stage flavour--lime" role="img" aria-label="Lime label with splashing green juice, leaves and lime halves">
    <div class="front-label">
      <div class="brand">KORVA</div><div class="brand-sub">NUTRITION</div>
      <div class="flavour-name">LIME</div>
      <div class="electrolytes-box">ELECTROLYTES</div>
      <div class="format">HYDRATION POWDER</div>
      <div class="label-body">
        <ul class="callouts">
          <li><svg class="callout-icon"><use href="#icon-keto"/></svg><span>KETO<br>FRIENDLY</span></li>
          <li><svg class="callout-icon"><use href="#icon-sugar"/></svg><span>SUGAR<br>FREE</span></li>
          <li><svg class="callout-icon"><use href="#icon-paleo"/></svg><span>PALEO<br>FRIENDLY</span></li>
          <li><svg class="callout-icon"><use href="#icon-gluten"/></svg><span>GLUTEN<br>FREE</span></li>
        </ul>
        <div class="fruit-art" role="img" aria-label="Illustration of a halved lime"></div>
      </div>
      <div class="net-weight">NET WT. 180g</div>
    </div>
  </div>
  <div class="stage flavour--watermelon" role="img" aria-label="Watermelon label with pink splashes and watermelon slices">
    <div class="front-label">
      <div class="brand">KORVA</div><div class="brand-sub">NUTRITION</div>
      <div class="flavour-name">WATERMELON</div>
      <div class="electrolytes-box">ELECTROLYTES</div>
      <div class="format">HYDRATION POWDER</div>
      <div class="label-body">
        <ul class="callouts">
          <li><svg class="callout-icon"><use href="#icon-keto"/></svg><span>KETO<br>FRIENDLY</span></li>
          <li><svg class="callout-icon"><use href="#icon-sugar"/></svg><span>SUGAR<br>FREE</span></li>
          <li><svg class="callout-icon"><use href="#icon-paleo"/></svg><span>PALEO<br>FRIENDLY</span></li>
          <li><svg class="callout-icon"><use href="#icon-gluten"/></svg><span>GLUTEN<br>FREE</span></li>
        </ul>
        <div class="fruit-art" role="img" aria-label="Illustration of a watermelon slice"></div>
      </div>
      <div class="net-weight">NET WT. 180g</div>
    </div>
  </div>
  <div class="stage flavour--mango" role="img" aria-label="Mango label with orange splashes, leaves and mango cubes">
    <div class="front-label">
      <div class="brand">KORVA</div><div class="brand-sub">NUTRITION</div>
      <div class="flavour-name">MANGO</div>
      <div class="electrolytes-box">ELECTROLYTES</div>
      <div class="format">HYDRATION POWDER</div>
      <div class="label-body">
        <ul class="callouts">
          <li><svg class="callout-icon"><use href="#icon-keto"/></svg><span>KETO<br>FRIENDLY</span></li>
          <li><svg class="callout-icon"><use href="#icon-sugar"/></svg><span>SUGAR<br>FREE</span></li>
          <li><svg class="callout-icon"><use href="#icon-paleo"/></svg><span>PALEO<br>FRIENDLY</span></li>
          <li><svg class="callout-icon"><use href="#icon-gluten"/></svg><span>GLUTEN<br>FREE</span></li>
        </ul>
        <div class="fruit-art" role="img" aria-label="Illustration of a ripe mango"></div>
      </div>
      <div class="net-weight">NET WT. 180g</div>
    </div>
  </div>
</section>

<!-- Label row: Strawberry -->
<section class="label-row label-row--1 flavour--strawberry">
  <div class="back-label">
    <div class="back-copy">
      <p><strong>Why rest when you can KORVA?</strong> Your body wasn’t made to run on sugar, chemicals, and artificial junk, and your hydration shouldn’t either. At <strong>KORVA</strong> Nutrition, we’ve created a clean, mineral-rich formula with Brindlemoor Flakes and essential electrolytes to fuel you the right way. No toxins, no fillers, just real ingredients that work with your body, not against it. Drink the way earth designed. Stay pure. <strong>KORVA.</strong></p>
      <p><strong>Directions:</strong> Mix 1 Scoop with 400-500ml of water &amp; Mix well before drinking. Do not exceed 2 servings per day.</p>
      <p>Manufactured by: <strong>KORVA</strong> Nutrition, 48 Ridgeway Lane, Perth, Australia. Contact: hello@korvamail.net | +61 400 555 012 Made in Australia | Batch No: 24817 | Best Before: 28/04/2026</p>
      <p class="store">Store in a cool, dry place below 30°C.<br>Reseal after use</p>
    </div>
    <div class="back-front">
      <div class="front-label front-label--inset">
        <div class="brand">KORVA</div><div class="brand-sub">NUTRITION</div>
        <div class="flavour-name">STRAWBERRY</div>
        <div class="electrolytes-box">ELECTROLYTES</div>
        <div class="format">HYDRATION POWDER</div>
        <div class="label-body">
          <ul class="callouts">
            <li><svg class="callout-icon"><use href="#icon-keto"/></svg><span>KETO<br>FRIENDLY</span></li>
            <li><svg class="callout-icon"><use href="#icon-sugar"/></svg><span>SUGAR<br>FREE</span></li>
            <li><svg class="callout-icon"><use href="#icon-paleo"/></svg><span>PALEO<br>FRIENDLY</span></li>
            <li><svg class="callout-icon"><use href="#icon-gluten"/></svg><span>GLUTEN<br>FREE</span></li>
          </ul>
          <div class="fruit-art" role="img" aria-label="Illustration of a ripe strawberry"></div>
        </div>
        <div class="net-weight">NET WT. 180g</div>
      </div>
    </div>
    <div class="back-panel">
      <div class="back-panel__top">
        <div class="nutrition">
          <div class="nutrition__title">Nutrition Information</div>
          <div>Servings per package: 36</div>
          <div>Serving size: 5.0 g</div>
          <table>
            <tr><th></th><th>Avg per serving</th><th>Avg per 100 g</th></tr>
            <tr><td>Energy</td><td>4 kJ</td><td>80 kJ</td></tr>
            <tr><td>Protein</td><td>0.0 g</td><td>0.0 g</td></tr>
            <tr><td>Fat, total</td><td>0.0 g</td><td>0.0 g</td></tr>
            <tr class="sub"><td>saturated</td><td>0.0 g</td><td>0.0 g</td></tr>
            <tr><td>Carbohydrate</td><td>0.0 g</td><td>0.0 g</td></tr>
            <tr class="sub"><td>sugars</td><td>0.0 g</td><td>0.0 g</td></tr>
            <tr><td>Sodium</td><td>1000 mg</td><td>20000 mg</td></tr>
            <tr><td>Potassium</td><td>200 mg</td><td>4000 mg</td></tr>
            <tr><td>Magnesium</td><td>60 mg</td><td>1200 mg</td></tr>
          </table>
        </div>
        <div class="made-badge" role="img" aria-label="Australian owned and made badge"></div>
      </div>
      <p class="ingredients"><strong>Ingredients:</strong> Sea Salt, Citric Acid, Brindlemoor Flakes®, Himalayan Pink Salt, Potassium Chloride, Magnesium Glycinate, Natural Flavour (e.g. Strawberry), Stevia Leaf Extract.</p>
    </div>
  </div>
  <div class="front-label">
    <div class="brand">KORVA</div><div class="brand-sub">NUTRITION</div>
    <div class="flavour-name">STRAWBERRY</div>
    <div class="electrolytes-box">ELECTROLYTES</div>
    <div class="format">HYDRATION POWDER</div>
    <div class="label-body">
      <ul class="callouts">
        <li><svg class="callout-icon"><use href="#icon-keto"/></svg><span>KETO<br>FRIENDLY</span></li>
        <li><svg class="callout-icon"><use href="#icon-sugar"/></svg><span>SUGAR<br>FREE</span></li>
        <li><svg class="callout-icon"><use href="#icon-paleo"/></svg><span>PALEO<br>FRIENDLY</span></li>
        <li><svg class="callout-icon"><use href="#icon-gluten"/></svg><span>GLUTEN<br>FREE</span></li>
      </ul>
      <div class="fruit-art" role="img" aria-label="Illustration of a ripe strawberry"></div>
    </div>
    <div class="net-weight">NET WT. 180g</div>
  </div>
</section>

<!-- Label row: Lime -->
<section class="label-row label-row--2 flavour--lime">
  <div class="back-label">
    <div class="back-copy">
      <p><strong>Why rest when you can KORVA?</strong> Your body wasn’t made to run on sugar, chemicals, and artificial junk, and your hydration shouldn’t either. At <strong>KORVA</strong> Nutrition, we’ve created a clean, mineral-rich formula with Brindlemoor Flakes and essential electrolytes to fuel you the right way. No toxins, no fillers, just real ingredients that work with your body, not against it. Drink the way earth designed. Stay pure. <strong>KORVA.</strong></p>
      <p><strong>Directions:</strong> Mix 1 Scoop with 400-500ml of water &amp; Mix well before drinking. Do not exceed 2 servings per day.</p>
      <p>Manufactured by: <strong>KORVA</strong> Nutrition, 48 Ridgeway Lane, Perth, Australia. Contact: hello@korvamail.net | +61 400 555 012 Made in Australia | Batch No: 24817 | Best Before: 28/04/2026</p>
      <p class="store">Store in a cool, dry place below 30°C.<br>Reseal after use</p>
    </div>
    <div class="back-front">
      <div class="front-label front-label--inset">
        <div class="brand">KORVA</div><div class="brand-sub">NUTRITION</div>
        <div class="flavour-name">LIME</div>
        <div class="electrolytes-box">ELECTROLYTES</div>
        <div class="format">HYDRATION POWDER</div>
        <div class="label-body">
          <ul class="callouts">
            <li><svg class="callout-icon"><use href="#icon-keto"/></svg><span>KETO<br>FRIENDLY</span></li>
            <li><svg class="callout-icon"><use href="#icon-sugar"/></svg><span>SUGAR<br>FREE</span></li>
            <li><svg class="callout-icon"><use href="#icon-paleo"/></svg><span>PALEO<br>FRIENDLY</span></li>
            <li><svg class="callout-icon"><use href="#icon-gluten"/></svg><span>GLUTEN<br>FREE</span></li>
          </ul>
          <div class="fruit-art" role="img" aria-label="Illustration of a whole lime"></div>
        </div>
        <div class="net-weight">NET WT. 180g</div>
      </div>
    </div>
    <div class="back-panel">
      <div class="back-panel__top">
        <div class="nutrition">
          <div class="nutrition__title">Nutrition Information</div>
          <div>Servings per package: 36</div>
          <div>Serving size: 5.0 g</div>
          <table>
            <tr><th></th><th>Avg per serving</th><th>Avg per 100 g</th></tr>
            <tr><td>Energy</td><td>4 kJ</td><td>80 kJ</td></tr>
            <tr><td>Protein</td><td>0.0 g</td><td>0.0 g</td></tr>
            <tr><td>Fat, total</td><td>0.0 g</td><td>0.0 g</td></tr>
            <tr class="sub"><td>saturated</td><td>0.0 g</td><td>0.0 g</td></tr>
            <tr><td>Carbohydrate</td><td>0.0 g</td><td>0.0 g</td></tr>
            <tr class="sub"><td>sugars</td><td>0.0 g</td><td>0.0 g</td></tr>
            <tr><td>Sodium</td><td>1000 mg</td><td>20000 mg</td></tr>
            <tr><td>Potassium</td><td>200 mg</td><td>4000 mg</td></tr>
            <tr><td>Magnesium</td><td>60 mg</td><td>1200 mg</td></tr>
          </table>
        </div>
        <div class="made-badge" role="img" aria-label="Australian owned and made badge"></div>
      </div>
      <p class="ingredients"><strong>Ingredients:</strong> Sea Salt, Citric Acid, Brindlemoor Flakes®, Himalayan Pink Salt, Potassium Chloride, Magnesium Glycinate, Natural Flavour (e.g. Lime), Stevia Leaf Extract.</p>
    </div>
  </div>
  <div class="front-label">
    <div class="brand">KORVA</div><div class="brand-sub">NUTRITION</div>
    <div class="flavour-name">LIME</div>
    <div class="electrolytes-box">ELECTROLYTES</div>
    <div class="format">HYDRATION POWDER</div>
    <div class="label-body">
      <ul class="callouts">
        <li><svg class="callout-icon"><use href="#icon-keto"/></svg><span>KETO<br>FRIENDLY</span></li>
        <li><svg class="callout-icon"><use href="#icon-sugar"/></svg><span>SUGAR<br>FREE</span></li>
        <li><svg class="callout-icon"><use href="#icon-paleo"/></svg><span>PALEO<br>FRIENDLY</span></li>
        <li><svg class="callout-icon"><use href="#icon-gluten"/></svg><span>GLUTEN<br>FREE</span></li>
      </ul>
      <div class="fruit-art" role="img" aria-label="Illustration of a whole lime"></div>
    </div>
    <div class="net-weight">NET WT. 180g</div>
  </div>
</section>

<!-- Label row: Mango -->
<section class="label-row label-row--3 flavour--mango">
  <div class="back-label">
    <div class="back-copy">
      <p><strong>Why rest when you can KORVA?</strong> Your body wasn’t made to run on sugar, chemicals, and artificial junk, and your hydration shouldn’t either. At <strong>KORVA</strong> Nutrition, we’ve created a clean, mineral-rich formula with Brindlemoor Flakes and essential electrolytes to fuel you the right way. No toxins, no fillers, just real ingredients that work with your body, not against it. Drink the way earth designed. Stay pure. <strong>KORVA.</strong></p>
      <p><strong>Directions:</strong> Mix 1 Scoop with 400-500ml of water &amp; Mix well before drinking. Do not exceed 2 servings per day.</p>
      <p>Manufactured by: <strong>KORVA</strong> Nutrition, 48 Ridgeway Lane, Perth, Australia. Contact: hello@korvamail.net | +61 400 555 012 Made in Australia | Batch No: 24817 | Best Before: 28/04/2026</p>
      <p class="store">Store in a cool, dry place below 30°C.<br>Reseal after use</p>
    </div>
    <div class="back-front">
      <div class="front-label front-label--inset">
        <div class="brand">KORVA</div><div class="brand-sub">NUTRITION</div>
        <div class="flavour-name">MANGO</div>
        <div class="electrolytes-box">ELECTROLYTES</div>
        <div class="format">HYDRATION POWDER</div>
        <div class="label-body">
          <ul class="callouts">
            <li><svg class="callout-icon"><use href="#icon-keto"/></svg><span>KETO<br>FRIENDLY</span></li>
            <li><svg class="callout-icon"><use href="#icon-sugar"/></svg><span>SUGAR<br>FREE</span></li>
            <li><svg class="callout-icon"><use href="#icon-paleo"/></svg><span>PALEO<br>FRIENDLY</span></li>
            <li><svg class="callout-icon"><use href="#icon-gluten"/></svg><span>GLUTEN<br>FREE</span></li>
          </ul>
          <div class="fruit-art" role="img" aria-label="Illustration of a ripe mango"></div>
        </div>
        <div class="net-weight">NET WT. 180g</div>
      </div>
    </div>
    <div class="back-panel">
      <div class="back-panel__top">
        <div class="nutrition">
          <div class="nutrition__title">Nutrition Information</div>
          <div>Servings per package: 36</div>
          <div>Serving size: 5.0 g</div>
          <table>
            <tr><th></th><th>Avg per serving</th><th>Avg per 100 g</th></tr>
            <tr><td>Energy</td><td>4 kJ</td><td>80 kJ</td></tr>
            <tr><td>Protein</td><td>0.0 g</td><td>0.0 g</td></tr>
            <tr><td>Fat, total</td><td>0.0 g</td><td>0.0 g</td></tr>
            <tr class="sub"><td>saturated</td><td>0.0 g</td><td>0.0 g</td></tr>
            <tr><td>Carbohydrate</td><td>0.0 g</td><td>0.0 g</td></tr>
            <tr class="sub"><td>sugars</td><td>0.0 g</td><td>0.0 g</td></tr>
            <tr><td>Sodium</td><td>1000 mg</td><td>20000 mg</td></tr>
            <tr><td>Potassium</td><td>200 mg</td><td>4000 mg</td></tr>
            <tr><td>Magnesium</td><td>60 mg</td><td>1200 mg</td></tr>
          </table>
        </div>
        <div class="made-badge" role="img" aria-label="Australian owned and made badge"></div>
      </div>
      <p class="ingredients"><strong>Ingredients:</strong> Sea Salt, Citric Acid, Brindlemoor Flakes®, Himalayan Pink Salt, Potassium Chloride, Magnesium Glycinate, Natural Flavour (e.g. Mango), Stevia Leaf Extract.</p>
    </div>
  </div>
  <div class="front-label">
    <div class="brand">KORVA</div><div class="brand-sub">NUTRITION</div>
    <div class="flavour-name">MANGO</div>
    <div class="electrolytes-box">ELECTROLYTES</div>
    <div class="format">HYDRATION POWDER</div>
    <div class="label-body">
      <ul class="callouts">
        <li><svg class="callout-icon"><use href="#icon-keto"/></svg><span>KETO<br>FRIENDLY</span></li>
        <li><svg class="callout-icon"><use href="#icon-sugar"/></svg><span>SUGAR<br>FREE</span></li>
        <li><svg class="callout-icon"><use href="#icon-paleo"/></svg><span>PALEO<br>FRIENDLY</span></li>
        <li><svg class="callout-icon"><use href="#icon-gluten"/></svg><span>GLUTEN<br>FREE</span></li>
      </ul>
      <div class="fruit-art" role="img" aria-label="Illustration of a ripe mango"></div>
    </div>
    <div class="net-weight">NET WT. 180g</div>
  </div>
</section>

<!-- Label row: Watermelon -->
<section class="label-row label-row--4 flavour--watermelon">
  <div class="back-label">
    <div class="back-copy">
      <p><strong>Why rest when you can KORVA?</strong> Your body wasn’t made to run on sugar, chemicals, and artificial junk, and your hydration shouldn’t either. At <strong>KORVA</strong> Nutrition, we’ve created a clean, mineral-rich formula with Brindlemoor Flakes and essential electrolytes to fuel you the right way. No toxins, no fillers, just real ingredients that work with your body, not against it. Drink the way earth designed. Stay pure. <strong>KORVA.</strong></p>
      <p><strong>Directions:</strong> Mix 1 Scoop with 400-500ml of water &amp; Mix well before drinking. Do not exceed 2 servings per day.</p>
      <p>Manufactured by: <strong>KORVA</strong> Nutrition, 48 Ridgeway Lane, Perth, Australia. Contact: hello@korvamail.net | +61 400 555 012 Made in Australia | Batch No: 24817 | Best Before: 28/04/2026</p>
      <p class="store">Store in a cool, dry place below 30°C.<br>Reseal after use</p>
    </div>
    <div class="back-front">
      <div class="front-label front-label--inset">
        <div class="brand">KORVA</div><div class="brand-sub">NUTRITION</div>
        <div class="flavour-name">WATERMELON</div>
        <div class="electrolytes-box">ELECTROLYTES</div>
        <div class="format">HYDRATION POWDER</div>
        <div class="label-body">
          <ul class="callouts">
            <li><svg class="callout-icon"><use href="#icon-keto"/></svg><span>KETO<br>FRIENDLY</span></li>
            <li><svg class="callout-icon"><use href="#icon-sugar"/></svg><span>SUGAR<br>FREE</span></li>
            <li><svg class="callout-icon"><use href="#icon-paleo"/></svg><span>PALEO<br>FRIENDLY</span></li>
            <li><svg class="callout-icon"><use href="#icon-gluten"/></svg><span>GLUTEN<br>FREE</span></li>
          </ul>
          <div class="fruit-art" role="img" aria-label="Illustration of a watermelon slice"></div>
        </div>
        <div class="net-weight">NET WT. 180g</div>
      </div>
    </div>
    <div class="back-panel">
      <div class="back-panel__top">
        <div class="nutrition">
          <div class="nutrition__title">Nutrition Information</div>
          <div>Servings per package: 36</div>
          <div>Serving size: 5.0 g</div>
          <table>
            <tr><th></th><th>Avg per serving</th><th>Avg per 100 g</th></tr>
            <tr><td>Energy</td><td>4 kJ</td><td>80 kJ</td></tr>
            <tr><td>Protein</td><td>0.0 g</td><td>0.0 g</td></tr>
            <tr><td>Fat, total</td><td>0.0 g</td><td>0.0 g</td></tr>
            <tr class="sub"><td>saturated</td><td>0.0 g</td><td>0.0 g</td></tr>
            <tr><td>Carbohydrate</td><td>0.0 g</td><td>0.0 g</td></tr>
            <tr class="sub"><td>sugars</td><td>0.0 g</td><td>0.0 g</td></tr>
            <tr><td>Sodium</td><td>1000 mg</td><td>20000 mg</td></tr>
            <tr><td>Potassium</td><td>200 mg</td><td>4000 mg</td></tr>
            <tr><td>Magnesium</td><td>60 mg</td><td>1200 mg</td></tr>
          </table>
        </div>
        <div class="made-badge" role="img" aria-label="Australian owned and made badge"></div>
      </div>
      <p class="ingredients"><strong>Ingredients:</strong> Sea Salt, Citric Acid, Brindlemoor Flakes®, Himalayan Pink Salt, Potassium Chloride, Magnesium Glycinate, Natural Flavour (e.g. Watermelon), Stevia Leaf Extract.</p>
    </div>
  </div>
  <div class="front-label">
    <div class="brand">KORVA</div><div class="brand-sub">NUTRITION</div>
    <div class="flavour-name">WATERMELON</div>
    <div class="electrolytes-box">ELECTROLYTES</div>
    <div class="format">HYDRATION POWDER</div>
    <div class="label-body">
      <ul class="callouts">
        <li><svg class="callout-icon"><use href="#icon-keto"/></svg><span>KETO<br>FRIENDLY</span></li>
        <li><svg class="callout-icon"><use href="#icon-sugar"/></svg><span>SUGAR<br>FREE</span></li>
        <li><svg class="callout-icon"><use href="#icon-paleo"/></svg><span>PALEO<br>FRIENDLY</span></li>
        <li><svg class="callout-icon"><use href="#icon-gluten"/></svg><span>GLUTEN<br>FREE</span></li>
      </ul>
      <div class="fruit-art" role="img" aria-label="Illustration of a watermelon slice"></div>
    </div>
    <div class="net-weight">NET WT. 180g</div>
  </div>
</section>

</body>
</html>
```